Brellwick Partners, LLC Stationary

Brellwick Partners, LLC is a new financial planning and consulting company. We are looking for designs on business cards, letterhead, envelopes, and anything else that would be useful. Our preference for business card design is two sided. We are looking for a professional and clean look with incorporating the logo and patriotic feel. Thank you to all who participate and good luck!

```html
<!DOCTYPE html>
<html lang="en">
<head>
<meta charset="utf-8">
<title>Brellwick Partners, LLC Stationery</title>
<link href="https://fonts.googleapis.com/css2?family=Arimo:wght@400;700&display=swap" rel="stylesheet">
<style>
  :root{
    --navy:#103d6a;
    --red:#c41f2a;
    --paper:#f4f3f1;
    --backdrop:#a9a8a9;
    --ink:#4a4a4a;
    --faint:#e7e6e8;
  }
  *{box-sizing:border-box;margin:0;padding:0}
  html,body{width:1200px;height:770px;overflow:hidden}
  body{background:var(--backdrop);font-family:"Arimo",Arial,sans-serif;color:var(--ink);position:relative}
  .sheet{position:absolute;background:var(--paper);overflow:hidden;box-shadow:2px 3px 6px rgba(0,0,0,.25)}
  .sheet svg.swoosh{position:absolute;left:0;top:0}
  .brand{display:flex;align-items:center;gap:6px;color:var(--navy);font-weight:700;letter-spacing:.02em;white-space:nowrap}
  .brand .dot{border-radius:50%;background:var(--navy);flex:none}
  .faint-mark{position:absolute;border-radius:50%;background:var(--faint)}
  .address{line-height:1.35}
  .contact{list-style:none;line-height:1.45}
  .contact li{display:flex;align-items:center;gap:4px}
  .contact svg{fill:var(--navy);flex:none}

  /* business card front */
  .card-front{left:86px;top:46px;width:218px;height:124px;background:#fff}
  .card-front .brand{position:absolute;left:14px;top:18px;font-size:10px}
  .card-front .brand .dot{width:11px;height:11px}
  .card-front .address{position:absolute;left:14px;top:60px;font-size:5.6px}
  .card-front .contact{position:absolute;left:14px;top:81px;font-size:5.6px}
  .card-front .person{position:absolute;left:150px;top:65px;text-align:right;width:68px;padding-right:9px}
  .card-front .person .name{color:var(--navy);font-weight:700;font-size:7.4px}
  .card-front .person .role{color:var(--red);font-size:5.2px;margin-top:1px}
  .card-front .person{left:140px;width:140px;left:78px}

  /* business card back */
  .card-back{left:338px;top:46px;width:218px;height:124px;background:var(--navy);color:#fff;display:flex;flex-direction:column;align-items:center;justify-content:center}
  .card-back .brand{color:#fff;font-size:12px}
  .card-back .brand .dot{background:#fff;width:12px;height:12px}
  .card-back .url{position:absolute;bottom:13px;font-size:5.4px;letter-spacing:.2em}

  /* envelope front */
  .envelope-front{left:62px;top:202px;width:560px;height:254px}
  .envelope-front .faint-mark{left:300px;top:10px;width:230px;height:230px}
  .envelope-front .brand{position:absolute;left:24px;top:30px;font-size:16px}
  .envelope-front .brand .dot{width:16px;height:16px}
  .envelope-front .address{position:absolute;left:24px;top:72px;font-size:8.8px}

  /* envelope back */
  .envelope-back{left:57px;top:479px;width:559px;height:255px}
  .envelope-back .flap{position:absolute;left:0;top:0}
  .envelope-back .flap-content{position:absolute;left:0;top:14px;width:100%;display:flex;flex-direction:column;align-items:center;color:#fff}
  .envelope-back .brand{color:#fff;font-size:13px}
  .envelope-back .brand .dot{background:#fff;width:13px;height:13px}
  .envelope-back .url{font-size:6.6px;letter-spacing:.2em;margin-top:22px}

  /* letterhead */
  .letterhead{left:643px;top:33px;width:497px;height:701px}
  .letterhead .faint-mark{left:85px;top:190px;width:330px;height:330px}
  .letterhead .brand{position:absolute;left:32px;top:54px;font-size:15px}
  .letterhead .brand .dot{width:15px;height:15px}
  .letterhead .details{position:absolute;left:370px;top:22px;font-size:8px}
  .letterhead .contact{margin-top:3px}
  .letterhead .contact svg{width:8px;height:8px}
</style>
</head>
<body>

<!-- Business card: front -->
<section class="sheet card-front">
  <svg class="swoosh" width="218" height="124" viewBox="0 0 218 124" aria-hidden="true">
    <path d="M168,0 Q238,55 190,124 L218,124 L218,0 Z" fill="var(--navy)"/>
    <path d="M140,0 Q232,42 180,124 L190,124 Q238,55 168,0 Z" fill="var(--red)" stroke="#fff" stroke-width="1"/>
  </svg>
  <div class="brand"><span class="dot"></span>Brellwick Partners, LLC</div>
  <p class="address">2170 Harlow Lane<br>Fenwick Bay, NY 10990</p>
  <ul class="contact">
    <li><svg width="6" height="6" viewBox="0 0 10 10"><path d="M2 0h2l1 3-1.5 1a6 6 0 0 0 2.5 2.5L7 5l3 1v2a2 2 0 0 1-2 2A8 8 0 0 1 0 2a2 2 0 0 1 2-2z"/></svg>555 0142 8831</li>
    <li><svg width="6" height="6" viewBox="0 0 10 10"><path d="M2 0h6v3H2zM0 4h10v4H8v2H2V8H0z"/></svg>555 0193 4470</li>
    <li><svg width="6" height="6" viewBox="0 0 10 10"><path d="M0 2h10v6H0zM0 2l5 3.5L10 2" /></svg>marcus@brellwick.com</li>
    <li><svg width="6" height="6" viewBox="0 0 10 10"><circle cx="5" cy="5" r="5"/></svg>www.brellwick.com</li>
  </ul>
  <div class="person" style="left:90px;width:84px;text-align:right;padding-right:0;top:66px">
    <p class="name">MARCUS TELL</p>
    <p class="role">PRESIDENT</p>
  </div>
</section>

<!-- Business card: back -->
<section class="sheet card-back">
  <div class="brand"><span class="dot"></span>Brellwick Partners, LLC</div>
  <p class="url">www.brellwick.com</p>
</section>

<!-- Envelope: front -->
<section class="sheet envelope-front">
  <div class="faint-mark" role="img" aria-label="Faint large brand mark watermark"></div>
  <svg class="swoosh" width="560" height="254" viewBox="0 0 560 254" aria-hidden="true">
    <path d="M560,120 Q540,222 436,254 L560,254 Z" fill="var(--navy)"/>
    <path d="M560,112 Q525,226 345,254 L436,254 Q540,222 560,124 Z" fill="var(--red)" stroke="#fff" stroke-width="1"/>
  </svg>
  <div class="brand"><span class="dot"></span>Brellwick Partners, LLC</div>
  <p class="address">2170 Harlow Lane<br>Fenwick Bay, NY 10990</p>
</section>

<!-- Envelope: back -->
<section class="sheet envelope-back">
  <svg class="flap" width="559" height="100" viewBox="0 0 559 100" aria-hidden="true">
    <path d="M0,0 L559,0 L548,64 Q544,94 514,94 L45,94 Q15,94 11,64 Z" fill="var(--navy)"/>
  </svg>
  <div class="flap-content">
    <div class="brand" style="margin-top:18px"><span class="dot"></span>Brellwick Partners, LLC</div>
    <p class="url">www.brellwick.com</p>
  </div>
</section>

<!-- Letterhead -->
<section class="sheet letterhead">
  <div class="faint-mark" role="img" aria-label="Faint large brand mark watermark"></div>
  <svg class="swoosh" width="497" height="701" viewBox="0 0 497 701" aria-hidden="true">
    <path d="M497,566 Q478,670 372,701 L497,701 Z" fill="var(--navy)"/>
    <path d="M497,556 Q470,676 283,701 L372,701 Q478,670 497,572 Z" fill="var(--red)" stroke="#fff" stroke-width="1"/>
  </svg>
  <div class="brand"><span class="dot"></span>Brellwick Partners, LLC</div>
  <div class="details">
    <p class="address">2170 Harlow Lane<br>Fenwick Bay, NY 10990</p>
    <ul class="contact">
      <li><svg viewBox="0 0 10 10"><path d="M2 0h2l1 3-1.5 1a6 6 0 0 0 2.5 2.5L7 5l3 1v2a2 2 0 0 1-2 2A8 8 0 0 1 0 2a2 2 0 0 1 2-2z"/></svg>555 0142 8831</li>
      <li><svg viewBox="0 0 10 10"><path d="M2 0h6v3H2zM0 4h10v4H8v2H2V8H0z"/></svg>555 0193 4470</li>
      <li><svg viewBox="0 0 10 10"><path d="M0 2h10v6H0z"/></svg>marcus@brellwick.com</li>
      <li><svg viewBox="0 0 10 10"><circle cx="5" cy="5" r="5"/></svg>www.brellwick.com</li>
    </ul>
  </div>
</section>

</body>
</html>
```